7:40 Command Blueprint- A Handbook To Shape The Captain Others Could Trust

7:40 Command Blueprint
A Handbook To Shape The Captain Others Could Trust

It will be a 6 X 9 guide that is meant for people to keep with them with pages to fill out. See supporting pics for overall pillars that are discussed and form basis of the solution.

I will need a spine and back cover as well.

My blog and content: www.corvinmhale-example.com

Target Market(s)

Business professionals, senior emergency services people

Industry/Entity Type

Business Management

Font styles to use
Serif

Colors

Designer to choose colors to be used in the design.

Requirements
Must have
• Clean look, easily recognizable among other books. Front cover and back and spine. My picture on the back somewhere (corner maybe?!)
Nice to have
• Easily recognizeable
• NOTE: Graphic should read Today, Was I the Leader That I Would Want? I uploaded graphic that says ..."I Would've Wanted" which is incorrect.
Should not have
• Busy cover

```html
<!DOCTYPE html>
<html lang="en">
<head>
<meta charset="utf-8">
<title>7:40 Command Blueprint – Book Cover Wrap</title>
<link rel="stylesheet" href="https://fonts.googleapis.com/css2?family=Bebas+Neue&family=Oswald:wght@400&family=Arimo:wght@400&display=swap">
<style>
  :root {
    --stage: #000000;
    --paper: #ffffff;
    --paper-shade: #e9e9e9;
    --accent-red: #c8141c;
    --ink: #1a1a1a;
    --rule: #555555;
    --fold-tone: #d9d9d9;
    --placeholder-light: #e4e4e4;
    --placeholder-dark: #c9c9c9;
  }
  * { margin: 0; padding: 0; box-sizing: border-box; }
  html, body { width: 1200px; height: 1200px; overflow: hidden; background: var(--stage); }
  .canvas { position: relative; width: 1200px; height: 1200px; background: var(--stage); }

  .wrap {
    position: absolute; left: 37px; top: 220px; width: 1115px; height: 748px;
    background: var(--paper); overflow: hidden;
  }
  .front-shade {
    position: absolute; left: 590px; top: 0; width: 525px; height: 748px;
    background: radial-gradient(ellipse at 55% 40%, #ffffff 0%, #f7f7f7 45%, var(--paper-shade) 100%);
  }
  .fold-field {
    position: absolute; left: 0; top: 560px; width: 1115px; height: 188px;
    background: linear-gradient(180deg, rgba(255,255,255,0) 0%, var(--fold-tone) 55%, #cfcfcf 100%);
  }

  /* Back cover */
  .back-title {
    position: absolute; left: 31px; top: 18px;
    font-family: "Bebas Neue", "Oswald", sans-serif; font-size: 55px; line-height: 1; font-weight: 400;
    color: var(--accent-red); letter-spacing: 0.5px; white-space: nowrap;
  }
  .back-copy {
    position: absolute; left: 31px; width: 450px;
    font-family: "Arimo", Arial, sans-serif; font-size: 12.4px; line-height: 16px;
    color: var(--ink); text-align: justify;
  }
  .back-copy.intro { top: 80px; }
  .back-copy.body { top: 212px; }
  .back-rule { position: absolute; left: 31px; top: 448px; width: 450px; height: 1px; background: var(--rule); }
  .author-photo {
    position: absolute; left: 35px; top: 477px; width: 104px; height: 138px; background: #000;
  }
  .author-bio {
    position: absolute; left: 157px; top: 472px; width: 324px;
    font-family: "Arimo", Arial, sans-serif; font-size: 12.2px; line-height: 16px;
    color: var(--ink); text-align: justify;
  }
  .website {
    position: absolute; left: 31px; top: 712px;
    font-family: "Arimo", Arial, sans-serif; font-size: 12.5px; color: var(--ink);
  }

  /* Spine */
  .spine-title { position: absolute; left: 584px; top: 27px; width: 0; height: 0; }
  .spine-title span {
    position: absolute; left: 0; top: 0; white-space: nowrap;
    transform: rotate(90deg); transform-origin: 0 0;
    font-family: "Bebas Neue", "Oswald", sans-serif; font-size: 50px; line-height: 1;
    color: var(--accent-red);
  }
  .spine-author { position: absolute; left: 567px; top: 576px; width: 0; height: 0; }
  .spine-author span {
    position: absolute; left: 0; top: 0; white-space: nowrap;
    transform: rotate(90deg); transform-origin: 0 0;
    font-family: "Oswald", sans-serif; font-size: 20px; line-height: 1; color: var(--ink);
    letter-spacing: 0.5px;
  }

  /* Front cover */
  .front-title {
    position: absolute; left: 646px; top: 10px; width: 440px; text-align: center;
    font-family: "Bebas Neue", "Oswald", sans-serif; color: var(--accent-red);
    line-height: 0.84; font-weight: 400;
  }
  .front-title .line-top { display: block; font-size: 140px; }
  .front-title .line-command { display: block; font-size: 112px; }
  .front-title .line-blueprint { display: block; font-size: 122px; }
  .front-subtitle {
    position: absolute; left: 646px; top: 346px; width: 440px; text-align: center;
    font-family: "Arimo", Arial, sans-serif; font-size: 13.4px; letter-spacing: 0.1px;
    color: var(--ink); text-transform: uppercase; padding-bottom: 6px;
    border-bottom: 1.5px solid var(--rule);
  }
  .compass-placeholder {
    position: absolute; left: 908px; top: 473px; width: 105px; height: 105px;
    background: linear-gradient(160deg, var(--placeholder-light) 0%, var(--placeholder-dark) 100%);
  }
  .front-author {
    position: absolute; left: 590px; top: 686px; width: 525px; text-align: center;
    font-family: "Oswald", sans-serif; font-size: 30px; letter-spacing: 1.5px;
    color: var(--ink); line-height: 1;
  }
</style>
</head>
<body>
<div class="canvas">
  <div class="wrap">
    <div class="front-shade"></div>
    <div class="fold-field" role="img" aria-label="Rows of small white paper boats on a pale grey ground"></div>

    <!-- Back cover -->
    <h2 class="back-title">7:40 Command Blueprint</h2>
    <p class="back-copy intro">Lorem ipsum dolor sit amet, consectetur adipiscing elit, sed do eiusmod tempor incididunt ut labore et dolore magna aliqua. Ut enim ad minim veniam, quis nostrud exercitation ullamco laboris nisi ut aliquip ex ea commodo consequat. Duis aute irure dolor in reprehenderit in voluptate velit esse cillum dolore eu fugiat nulla pariatur. Excepteur sint occaecat cupidatat non proident, sunt in culpa qui officia deserunt mollit anim id est laborum.</p>
    <p class="back-copy body">Sed ut perspiciatis unde omnis iste natus error sit voluptatem accusantium doloremque laudantium, totam rem aperiam, eaque ipsa quae ab illo inventore veritatis et quasi architecto beatae vitae dicta sunt explicabo. Nemo enim ipsam voluptatem quia voluptas sit aspernatur aut odit aut fugit, sed quia consequuntur magni dolores eos qui ratione voluptatem sequi nesciunt. Neque porro quisquam est, qui dolorem ipsum quia dolor sit amet, consectetur, adipisci velit, sed quia non numquam eius modi tempora incidunt ut labore et dolore magnam aliquam quaerat voluptatem. Ut enim ad minima veniam, quis nostrum exercitationem ullam corporis suscipit laboriosam, nisi ut aliquid ex ea commodi consequatur? Quis autem vel eum iure reprehenderit qui in ea voluptate velit esse quam nihil molestiae consequatur, vel illum qui dolorem eum fugiat quo voluptas nulla pariatur?</p>
    <div class="back-rule"></div>
    <div class="author-photo" role="img" aria-label="Author portrait placeholder"></div>
    <p class="author-bio">Lorem ipsum dolor sit amet, consectetur adipiscing elit, sed do eiusmod tempor incididunt ut labore et dolore magna aliqua. Ut enim ad minim veniam, quis nostrud exercitation ullamco laboris nisi ut aliquip ex ea commodo consequat. Duis aute irure dolor in reprehenderit in voluptate velit esse cillum dolore eu fugiat nulla pariatur. Excepteur sint occaecat cupidatat non proident, sunt in culpa qui officia deserunt mollit anim id est laborum.</p>
    <p class="website">www.corvinmhale-example.com</p>

    <!-- Spine -->
    <div class="spine-title"><span>7:40 Command Blueprint</span></div>
    <div class="spine-author"><span>CORVIN M. HALE</span></div>

    <!-- Front cover -->
    <h1 class="front-title">
      <span class="line-top">7:40</span>
      <span class="line-command">Command</span>
      <span class="line-blueprint">Blueprint</span>
    </h1>
    <p class="front-subtitle">A Handbook To Shape The Captain Others Could Trust</p>
    <div class="compass-placeholder" role="img" aria-label="Illustration of a compass with a red needle and a dotted trail leading to it"></div>
    <p class="front-author">CORVIN M. HALE</p>
  </div>
</div>
</body>
</html>
```